Business card for Luxury Portable Restroom Trailer company

We are a Luxury Portable Restroom Trailer Company Called FALCRIDGE HIRES. Based in Orange County California. We provide portable restroom trailers for events, such as, Weddings, Concerts, Charity events, Sporting events, Tournaments, Corporate events, ect. We rent and Sell the Luxury restrooms. Our colors are white, grey, and Orange. As you will see in the logo we uploaded.
There are 2 people in the company so the names and titles will change for the 3 people but card will remain the same. Here is the information for each Person: Dwight Penner CFO 555 318-0476
next Person: Leon Marchetti VP 555 318-0476
Next Person: Owen Marchetti CEO 555 318-0476
Information to include on the card: Luxury Restroom Trailers Rental and Sales. Weddings, Concerts, Charity, Sporting and Corp. Events.

```html
<!DOCTYPE html>
<html lang="en">
<head>
<meta charset="utf-8">
<title>Falcridge Hires – Business Card</title>
<link href="https://fonts.googleapis.com/css2?family=Archivo:wght@400;700&display=swap" rel="stylesheet">
<style>
  :root {
    --page: #e6e6e6;
    --card-grey: #4a4a4d;
    --card-white: #ffffff;
    --accent: #e8621f;
    --ink-dark: #4a4a4d;
    --ink-light: #ffffff;
  }
  * { box-sizing: border-box; margin: 0; padding: 0; }
  html, body {
    width: 1200px; height: 800px; overflow: hidden;
    background: var(--page);
    font-family: "Archivo", Arial, sans-serif;
  }
  .stage {
    width: 1200px; height: 800px;
    display: flex; align-items: center; justify-content: center; gap: 50px;
  }
  .card {
    position: relative;
    width: 525px; height: 300px;
    border-radius: 16px;
    overflow: hidden;
    background: var(--card-grey);
    box-shadow: 0 3px 0 var(--accent), 0 10px 24px rgba(0,0,0,.18);
  }
  .card-shape { position: absolute; inset: 0; }

  /* Front: person details */
  .front-brand {
    position: absolute; left: 345px; top: 92px; width: 170px;
    text-align: center;
    color: var(--ink-dark);
    font-weight: 700; font-size: 22px; line-height: 1.1; letter-spacing: 1px;
  }
  .person { position: absolute; left: 32px; top: 62px; color: var(--ink-light); }
  .person-name {
    color: var(--accent); font-weight: 700; font-size: 21px;
    text-transform: uppercase; letter-spacing: .5px;
  }
  .person-title { font-size: 14px; margin-top: 2px; }
  .address { margin-top: 34px; font-size: 13px; line-height: 1.35; }
  .contacts { margin-top: 18px; list-style: none; font-size: 13px; line-height: 1.45; }
  .contacts li { display: flex; align-items: center; gap: 7px; }
  .contacts svg { width: 11px; height: 11px; flex: none; }

  /* Back: brand side */
  .back-brand {
    position: absolute; left: 0; right: 0; top: 98px;
    display: flex; align-items: center; justify-content: center; gap: 12px;
    color: var(--ink-light); font-weight: 700; font-size: 38px; letter-spacing: 1px;
  }
  .brand-square { width: 16px; height: 16px; background: var(--accent); }
  .tagline {
    position: absolute; left: 0; right: 0; bottom: 52px;
    text-align: center; color: var(--ink-light);
    font-size: 14px; line-height: 1.45;
  }
</style>
</head>
<body>
<main class="stage">

  <section class="card card-front" aria-label="Business card front">
    <svg class="card-shape" viewBox="0 0 525 300" aria-hidden="true">
      <polygon points="318,0 525,0 525,300 392,300 294,268" fill="var(--card-white)"/>
      <polygon points="326,0 525,0 525,300 404,300 300,262" fill="var(--accent)"/>
      <polygon points="336,0 525,0 525,300 420,300 310,254" fill="var(--card-white)"/>
    </svg>
    <div class="front-brand">FALCRIDGE<br>HIRES</div>

    <div class="person">
      <h1 class="person-name">Dwight Penner</h1>
      <p class="person-title">CFO</p>
      <p class="address">2170 Harbor Crest Lane<br>Tustin, CA 92780</p>
      <ul class="contacts">
        <li>
          <svg viewBox="0 0 12 12" aria-hidden="true"><path d="M2.5 1h2l1 3-1.3 1a6 6 0 0 0 2.8 2.8l1-1.3 3 1v2a1 1 0 0 1-1 1A9 9 0 0 1 1.5 2a1 1 0 0 1 1-1z" fill="var(--accent)"/></svg>
          555 318-0476
        </li>
        <li>
          <svg viewBox="0 0 12 12" aria-hidden="true"><rect x="0.5" y="2" width="11" height="8" fill="var(--accent)"/><path d="M0.5 2.5 6 6.5l5.5-4" stroke="var(--card-grey)" fill="none"/></svg>
          name@falcridge.com
        </li>
        <li>
          <svg viewBox="0 0 12 12" aria-hidden="true"><circle cx="6" cy="6" r="5.5" fill="var(--accent)"/><path d="M.5 6h11M6 .5c-2.5 3-2.5 8 0 11M6 .5c2.5 3 2.5 8 0 11" stroke="var(--card-grey)" stroke-width=".8" fill="none"/></svg>
          www.falcridge.com
        </li>
      </ul>
    </div>
  </section>

  <section class="card card-back" aria-label="Business card back">
    <div class="back-brand"><span class="brand-square"></span>FALCRIDGE HIRES</div>
    <p class="tagline">Luxury Restroom Trailers Rental and Sales<br>Weddings, Concerts, Charity, Sporting and Corp Events</p>
  </section>

</main>
</body>
</html>
```